Book Title: The Weaver's Lantern. Author Name: Maribel Trowcastle

We are needing a cover, spine and back cover design for a poetry book that we are publishing called The Weaver's Lantern. We are looking for an elegant, and simplistic design with a very natural, dynamic and powerful impact.

Design Idea #1 - Shiva Conch Shell with a pink or black background. See Paul Renwick Image attached for design inspiration. Simple and dynamic .
Title and Author name created in same style as the attached Paul Renwick's Harbors and Lanterns image.

Design Idea #2 - Image of cauldron on (see cauldrons attached for ideas) black background.
See Paul Renwick Image attached for design inspiration. Simple and dynamic Title and Author name created in same style as the attached Paul Renwick's Harbors and Lanterns image

Design Idea #3 - Image of Tree of Life (see attached images for idea of what we are looking for) Would like to see on plain white, green, black and green background.

Target Market(s)

Spiritual Women, healers, visionaries,Goddess'

Requirements
Must have
• Please see project descriptions for specific design concepts we are looking for. Please include the authors name: Maribel Trowcastle on front, spine and back cover of the book

```html
<!DOCTYPE html>
<html lang="en">
<head>
<meta charset="utf-8">
<title>The Weaver's Lantern — Spine and Front Cover</title>
<link rel="stylesheet" href="https://fonts.googleapis.com/css2?family=EB+Garamond:wght@500&display=swap">
<style>
  :root {
    --backdrop: #f1f1f1;
    --paper: #ffffff;
    --ink: #111111;
    --fold: #e4e4e4;
    --emblem-ring: #c9c9c9;
    --emblem-field: #ffffff;
  }
  * { margin: 0; padding: 0; box-sizing: border-box; }
  html, body {
    width: 1200px;
    height: 1200px;
    overflow: hidden;
    background: var(--backdrop);
  }
  .canvas {
    position: relative;
    width: 1200px;
    height: 1200px;
  }
  .book {
    position: absolute;
    left: 249px;
    top: 60px;
    width: 702px;
    height: 1080px;
    display: flex;
    font-family: "EB Garamond", Georgia, serif;
    font-weight: 500;
    color: var(--ink);
    box-shadow: 0 0 0 1px rgba(0,0,0,0.06);
  }

  /* Spine */
  .spine {
    position: relative;
    width: 48px;
    height: 100%;
    background: var(--paper);
    border-right: 1px solid var(--fold);
  }
  .spine-text {
    position: absolute;
    left: 50%;
    writing-mode: vertical-rl;
    transform: translateX(-50%);
    font-size: 22px;
    line-height: 1;
    letter-spacing: 0.06em;
    text-transform: uppercase;
    white-space: nowrap;
  }
  .spine-title { top: 48px; }
  .spine-author { top: 712px; }
  .spine-emblem {
    position: absolute;
    left: 50%;
    top: 582px;
    width: 34px;
    height: 34px;
    margin-left: -17px;
  }

  /* Front cover */
  .front-cover {
    position: relative;
    flex: 1;
    height: 100%;
    background: var(--paper);
    text-align: center;
  }
  .cover-line {
    position: absolute;
    left: 0;
    right: 0;
    height: 80px;
    line-height: 80px;
    text-transform: uppercase;
    white-space: nowrap;
  }
  .cover-title .cover-line {
    font-size: 66px;
    letter-spacing: 0.2em;
    padding-left: 0.2em;
  }
  .cover-title .line-1 { top: 43px; }
  .cover-title .line-2 { top: 146px; }
  .cover-title .line-3 { top: 242px; }
  .emblem {
    position: absolute;
    left: 50%;
    top: 482px;
    width: 234px;
    height: 234px;
    margin-left: -117px;
  }
  .cover-author .cover-line {
    font-size: 60px;
    letter-spacing: 0.16em;
    padding-left: 0.16em;
  }
  .cover-author .line-1 { top: 854px; }
  .cover-author .line-2 { top: 954px; }
</style>
</head>
<body>
  <main class="canvas">
    <div class="book">
      <aside class="spine">
        <span class="spine-text spine-title">The Weaver's Lantern</span>
        <svg class="spine-emblem" viewBox="0 0 34 34" role="img" aria-label="Small Tree of Life illustration in a circular frame">
          <circle cx="17" cy="17" r="16" fill="var(--emblem-field)" stroke="var(--emblem-ring)" stroke-width="1.2"/>
          <circle cx="17" cy="17" r="12.5" fill="#2e2e2e" opacity="0.8"/>
        </svg>
        <span class="spine-text spine-author">Maribel Trowcastle</span>
      </aside>

      <section class="front-cover">
        <h1 class="cover-title">
          <span class="cover-line line-1">The</span>
          <span class="cover-line line-2">Weaver's</span>
          <span class="cover-line line-3">Lantern</span>
        </h1>

        <svg class="emblem" viewBox="0 0 234 234" role="img" aria-label="Tree of Life illustration with spreading branches and roots inside a rope-edged circular frame">
          <defs>
            <radialGradient id="emblem-tone" cx="50%" cy="45%" r="55%">
              <stop offset="0%" stop-color="#3a3a3a"/>
              <stop offset="100%" stop-color="#1e1e1e"/>
            </radialGradient>
          </defs>
          <circle cx="117" cy="117" r="114" fill="var(--emblem-field)" stroke="var(--emblem-ring)" stroke-width="5"/>
          <circle cx="117" cy="117" r="95" fill="url(#emblem-tone)" opacity="0.85"/>
        </svg>

        <p class="cover-author">
          <span class="cover-line line-1">Maribel</span>
          <span class="cover-line line-2">Trowcastle</span>
        </p>
      </section>
    </div>
  </main>
</body>
</html>
```